Business Card Design Project

We are rebranding an existing automotive collision repair business. The business is called dent haven. I have attached logo but I'm not tied to that. I want to leave this wide open.

I want this card to say we are professional, competent, cutting edge. We are focused on customers and use a lot of the latest technology to make the customer experience different. We sign customers in on iPads. Paperwork I signed electronically and updates are sent via text, email, logging on a website or as they wish. I want this innovation and image to come through in our cards

Target Market(s)

60%. Women 40% men. Age 35-60

Industry/Entity Type

Automotive

Requirements
Must have
• The card must have name, title, phone,email, cell, web page

```html
<!DOCTYPE html>
<html lang="en">
<head>
<meta charset="utf-8">
<title>dent haven — Business Card</title>
<link rel="stylesheet" href="https://fonts.googleapis.com/css2?family=PT+Sans:wght@400;700&family=PT+Sans+Narrow:wght@700&display=swap">
<style>
  :root {
    --stage: #dcdcde;
    --green: #78b43a;
    --green-deep: #5f9a26;
    --green-soft: #c9dfae;
    --green-pale: #e4efd6;
    --paper: #ffffff;
    --paper-shade: #e6e6e8;
    --ink: #4a4a4a;
    --ink-dark: #222222;
  }
  * { margin: 0; padding: 0; box-sizing: border-box; }
  html, body { width: 883px; height: 1200px; overflow: hidden; }
  body {
    background: var(--stage);
    font-family: "PT Sans", Arial, sans-serif;
    position: relative;
  }
  .card {
    position: absolute;
    left: 92px;
    width: 700px;
    height: 400px;
    overflow: hidden;
    box-shadow: 0 6px 18px rgba(0,0,0,0.18);
  }
  .card--front { top: 140px; background: linear-gradient(135deg, #82bd42 0%, var(--green) 55%, #6ea934 100%); }
  .card--back  { top: 660px; background: var(--paper); }

  .wordmark {
    font-family: "PT Sans Narrow", "PT Sans", sans-serif;
    font-weight: 700;
    letter-spacing: 0.5px;
    line-height: 1;
    display: flex;
    align-items: center;
    gap: 14px;
  }
  .wordmark__dot { width: 14px; height: 14px; border-radius: 50%; }
  .tagline {
    font-size: 13px;
    font-weight: 700;
    letter-spacing: 4px;
    text-transform: uppercase;
  }

  /* front */
  .front__brand {
    position: absolute; top: 120px; left: 0; right: 0;
    display: flex; flex-direction: column; align-items: center; gap: 12px;
    color: var(--paper);
  }
  .front__brand .wordmark { font-size: 66px; }
  .front__brand .wordmark__dot { background: var(--paper); }
  .front__rule { width: 420px; height: 1px; background: rgba(255,255,255,0.55); }
  .front__web {
    position: absolute; top: 290px; left: 0; right: 0; text-align: center;
    color: var(--paper); font-size: 19px;
  }

  /* back */
  .back__art { position: absolute; inset: 0; }
  .back__brand {
    position: absolute; top: 40px; left: 0; right: 0;
    display: flex; flex-direction: column; align-items: center; gap: 8px;
  }
  .back__brand .wordmark { font-size: 64px; color: var(--green); }
  .back__brand .wordmark__dot { background: var(--green); }
  .back__brand .tagline { color: var(--ink-dark); font-size: 12px; }
  .person { position: absolute; left: 110px; top: 262px; }
  .person__name { color: var(--green-deep); font-weight: 700; font-size: 20px; }
  .person__title { color: var(--ink); font-size: 15px; margin-top: 2px; }
  .contact { position: absolute; left: 465px; top: 228px; list-style: none; }
  .contact li {
    display: flex; align-items: center; gap: 8px;
    color: var(--ink); font-size: 17px; line-height: 26px;
  }
  .contact svg { width: 12px; height: 12px; fill: var(--green-deep); flex: none; }
</style>
</head>
<body>

<section class="card card--front" aria-label="Card front">
  <div class="front__brand">
    <div class="wordmark"><span class="wordmark__dot"></span>dent haven</div>
    <div class="front__rule"></div>
    <div class="tagline">Expert care for every car</div>
  </div>
  <div class="front__web">www.denthaven.com</div>
</section>

<section class="card card--back" aria-label="Card back">
  <svg class="back__art" viewBox="0 0 700 400" preserveAspectRatio="none" aria-hidden="true">
    <defs>
      <linearGradient id="paperFade" x1="0" y1="0" x2="1" y2="0">
        <stop offset="0" stop-color="#ffffff"/>
        <stop offset="1" stop-color="#e8e8ea"/>
      </linearGradient>
      <linearGradient id="greenFade" x1="0" y1="0" x2="1" y2="0">
        <stop offset="0" stop-color="#c7ddab"/>
        <stop offset="1" stop-color="#e6f0da"/>
      </linearGradient>
    </defs>
    <rect width="700" height="400" fill="url(#paperFade)"/>
    <path d="M0 225 C 200 255, 420 215, 700 180 L700 400 L0 400 Z" fill="url(#greenFade)"/>
    <path d="M240 236 C 420 225, 560 200, 700 180 L700 196 C 560 210, 420 230, 240 236 Z" fill="#78b43a"/>
  </svg>

  <div class="back__brand">
    <div class="wordmark"><span class="wordmark__dot"></span>dent haven</div>
    <div class="tagline">Expert care for every car</div>
  </div>

  <div class="person">
    <div class="person__name">Mara Ellison</div>
    <div class="person__title">Managing Director</div>
  </div>

  <ul class="contact">
    <li><svg viewBox="0 0 12 12"><path d="M2.5 0.8 L4.6 3.1 3.6 4.4 C4.3 6 5.9 7.6 7.6 8.4 L8.9 7.4 11.2 9.5 9.8 11.2 C5.2 10.6 1.4 6.8 0.8 2.2 Z"/></svg>555.0142.7730</li>
    <li><svg viewBox="0 0 12 12"><path d="M3 0 H9 V12 H3 Z M4 1.5 V9 H8 V1.5 Z M5.5 10 H6.5 V11 H5.5 Z" fill-rule="evenodd"/></svg>555.0142.7731</li>
    <li><svg viewBox="0 0 12 12"><path d="M3 0 H9 V3 H3 Z M0 4 H12 V9 H10 V12 H2 V9 H0 Z M3 8 V11 H9 V8 Z" fill-rule="evenodd"/></svg>555.0142.7732</li>
    <li><svg viewBox="0 0 12 12"><path d="M0 2 H12 V10 H0 Z M1 3 L6 6.5 11 3 V3.2 L6 7.6 1 3.2 Z" fill-rule="evenodd"/></svg>info@denthaven.com</li>
    <li><svg viewBox="0 0 12 12"><path d="M6 0 A6 6 0 1 0 6 12 A6 6 0 1 0 6 0 Z M6 1.3 A4.7 4.7 0 1 1 6 10.7 A4.7 4.7 0 1 1 6 1.3 Z M1 5.5 H11 V6.5 H1 Z M5.5 1 H6.5 V11 H5.5 Z" fill-rule="evenodd"/></svg>www.denthaven.com</li>
  </ul>
</section>

</body>
</html>
```